Travel Agency Website - Simple General

Need a 7 page simple design that is pretty repetitive. Need to be able to load quickly that is SEO optimized. Trying to give ideas on what they can do, be personal as we are local, but at the same time come across as professional and get information easily with little burden.

- Landing Page
- Brimwell Vacations Page
- Family Trips
- Road Trips from Texas
- Other Destinations
- About Us Page
- Contact Us Page

Target Market(s)

Families

Coding

Coded - Design and coding required

Number of Pages Required

5+ page

Colors

Designer to choose colors to be used in the design.

Requirements
Must have
• Like it to flow easily with our logo. Use that for colors, etc.

```html
<!DOCTYPE html>
<html lang="en">
<head>
<meta charset="utf-8">
<title>Family Trips Page – Meadowlark Travel Co.</title>
<link rel="stylesheet" href="https://fonts.googleapis.com/css2?family=Outfit:wght@400;500;600;700;800&display=swap">
<style>
:root{
  --board:#a2a2a2;
  --teal:#1d5a66;
  --teal-dark:#174a55;
  --gold:#c49a4c;
  --gold-light:#e3c27e;
  --ink:#2c4a52;
  --line:#b9c6c8;
  --page-top:#eef3f4;
  --page-bottom:#f2f0e8;
  --white:#ffffff;
}
*{box-sizing:border-box;margin:0;padding:0}
html,body{width:1200px;height:991px;overflow:hidden;background:var(--board)}
body{font-family:"Outfit",sans-serif;color:var(--ink)}
.board{position:absolute;left:0;top:0;width:2102px;height:1736px;transform:scale(0.57088);transform-origin:0 0;background:var(--board)}
.board-title{position:absolute;left:0;right:0;top:62px;text-align:center;color:var(--white);font-weight:700;font-size:114px;letter-spacing:2px;line-height:1}

.page{position:absolute;width:880px;background:linear-gradient(180deg,var(--page-top) 0%,#f1f4f3 55%,var(--page-bottom) 100%);overflow:hidden}
.page-left{left:138px;top:284px;height:1192px}
.page-right{left:1085px;top:283px;height:1302px}

.hills{position:absolute;left:0;width:880px;height:260px}
.page-left .hills{top:560px}
.page-right .hills{top:660px}

.contact-bar{position:absolute;left:400px;top:0;width:409px;height:29px;background:var(--teal);border-radius:0 0 8px 8px;display:flex;align-items:center;justify-content:center;gap:18px;color:var(--white);font-size:10.5px;font-weight:500;z-index:3}
.contact-bar span{display:flex;align-items:center;gap:6px}
.contact-bar svg{width:17px;height:17px}

.brand{position:absolute;left:62px;top:30px;width:140px;display:flex;align-items:center;gap:8px;z-index:3}
.brand-dot{flex:none;width:26px;height:26px;border-radius:50%;background:var(--gold)}
.brand-name{font-weight:700;font-size:17px;line-height:1.1;color:var(--teal)}

.nav{position:absolute;left:230px;top:46px;height:28px;display:flex;align-items:center;font-size:11px;font-weight:400;color:var(--teal-dark);z-index:3}
.nav a{color:inherit;text-decoration:none;margin-right:16px;position:relative}
.nav a.active{color:var(--teal)}
.nav a.active::after{content:"";position:absolute;left:0;right:0;bottom:-6px;height:2px;background:var(--gold)}
.nav .home{width:11px;height:11px;margin-right:16px}
.nav .about{margin-left:8px}
.btn-contact{display:flex;align-items:center;gap:12px;height:28px;padding:0 5px 0 18px;border-radius:14px;background:var(--gold);color:var(--white);font-size:10.5px;font-weight:500}
.arrow-dot{display:flex;align-items:center;justify-content:center;width:19px;height:19px;border-radius:50%;background:var(--gold-light)}
.arrow-dot svg{width:9px;height:9px}

.hero-photo{position:absolute}
.page-left .hero-photo{left:560px;top:70px;width:320px;height:250px;opacity:.45;border-radius:0 0 0 120px;background:linear-gradient(180deg,#cfe0ea 0%,#e2cbb8 45%,#bcd3dd 100%)}
.page-right .hero-photo{left:420px;top:100px;width:460px;height:330px;border-radius:200px 0 0 0;background:linear-gradient(165deg,#a9cdea 0%,#8fbfe4 22%,#e98e7a 44%,#f3c94a 58%,#e46a5e 74%,#3f5f86 100%)}

.eyebrow{position:absolute;font-size:16px;color:var(--teal-dark);letter-spacing:.3px}
.headline{position:absolute;font-weight:700;line-height:37px;color:var(--teal)}
.lede{position:absolute;font-size:15px;line-height:19px;color:var(--ink)}
.spark{position:absolute;color:var(--gold);font-size:13px}
.page-left .eyebrow{left:0;right:0;top:118px;text-align:center}
.page-left .headline{left:0;right:0;top:141px;text-align:center;font-size:37px}
.page-left .lede{left:140px;right:140px;top:224px;text-align:center}
.page-left .hero-spark{left:598px;top:130px}
.page-right .eyebrow{left:88px;top:166px}
.page-right .headline{left:88px;top:190px;font-size:34px}
.page-right .lede{left:88px;top:280px;width:305px}
.page-right .hero-spark{left:372px;top:181px}

.gallery{position:absolute;width:732px;height:268px;display:grid;grid-template-columns:repeat(4,1fr);grid-template-rows:1fr 1fr;gap:7px}
.page-left .gallery{left:75px;top:312px}
.page-right .gallery{left:86px;top:430px}
.tile{border-radius:3px}
.tall{grid-row:span 2}
.t1{background:linear-gradient(180deg,#cfe3ee 0%,#b08a6c 30%,#2f8fa3 60%,#8a7d70 100%)}
.t2{background:linear-gradient(180deg,#5c98d8 0%,#dbe9f5 25%,#3d9cc2 42%,#f08a2f 60%,#e56a2a 78%,#2fae8f 100%)}
.t3{background:linear-gradient(180deg,#c8dbe3 0%,#8fb6c2 35%,#d7c7a4 60%,#3e4c5a 100%)}
.t4{background:linear-gradient(165deg,#f0e7d5 0%,#d6c39c 35%,#c9cfd6 60%,#5c4335 85%,#2d2522 100%)}
.t5{background:linear-gradient(180deg,#a9c4d8 0%,#b98c6a 35%,#6b5447 60%,#c79a6c 100%)}
.t6{background:linear-gradient(180deg,#b3cbe0 0%,#e6e1d7 35%,#6f8ca0 55%,#c64a3a 80%,#3e3a36 100%)}

.plan-card{position:absolute;width:733px;height:443px;background:rgba(247,249,248,.8);border:1px solid #d4dcdc;border-radius:4px}
.page-left .plan-card{left:79px;top:642px}
.page-right .plan-card{left:83px;top:749px}
.plan-title{position:absolute;left:0;right:0;top:34px;text-align:center;font-weight:700;font-size:23px;color:var(--teal);letter-spacing:.3px}
.plan-card .spark{left:503px;top:22px}
.label{position:absolute;font-size:12.5px;font-weight:400;color:var(--teal-dark)}
.field{position:absolute;height:41px;border:1px solid var(--line);border-radius:3px;background:var(--white);display:flex;align-items:center;padding:0 18px;font-size:12.5px;color:#5d7378}
.field.select{justify-content:space-between}
.field svg{width:13px;height:13px}
.field.date{gap:8px;padding:0 12px;color:var(--teal-dark)}
.field.notes{align-items:flex-start;padding-top:14px;height:81px}
.btn-plan{position:absolute;left:277px;top:372px;width:184px;height:37px;border-radius:19px;background:var(--gold);color:var(--white);font-weight:600;font-size:15px;display:flex;align-items:center;justify-content:flex-end;gap:12px;padding-right:7px}
.btn-plan .arrow-dot{width:24px;height:24px}

.footer{position:absolute;left:0;right:0;bottom:0;height:54px;background:var(--white);font-size:10px;color:#3d4f53}
.footer p{position:absolute;left:0;width:844px;top:21px;text-align:center}
.social{position:absolute;left:722px;top:14px;display:flex;gap:7px}
.social span{width:16px;height:16px;border-radius:50%;background:var(--teal)}
</style>
</head>
<body>
<div class="board">
  <h1 class="board-title">FAMILY TRIPS PAGE</h1>

  <section class="page page-left">
    <svg class="hills" viewBox="0 0 880 260" preserveAspectRatio="none" aria-hidden="true"><path d="M0 120 L160 60 L300 130 L420 80 L560 140 L700 70 L880 110 V260 H0Z" fill="#dfe8e7" opacity=".7"/><path d="M0 170 L200 120 L380 170 L560 130 L760 170 L880 150 V260 H0Z" fill="#d6e2e0" opacity=".6"/></svg>
    <div class="hero-photo" role="img" aria-label="Faded photo of a smiling family on a sailboat deck"></div>
    <div class="contact-bar">
      <span><svg viewBox="0 0 20 20"><circle cx="10" cy="10" r="10" fill="#fff"/><rect x="5" y="6.5" width="10" height="7" rx="1" fill="none" stroke="#1d5a66" stroke-width="1.3"/><path d="M5.5 7l4.5 3.5L14.5 7" fill="none" stroke="#1d5a66" stroke-width="1.3"/></svg>hello@meadowlarktravel.example</span>
      <span><svg viewBox="0 0 20 20"><circle cx="10" cy="10" r="10" fill="#fff"/><path d="M7 5.5l2 2-1 1.5c.7 1.4 1.6 2.3 3 3l1.5-1 2 2-1.3 1.6c-3.5-.2-7-3.7-7.3-7.3z" fill="#1d5a66"/></svg>Phone Number (555) 010 2040</span>
    </div>
    <div class="brand"><span class="brand-dot"></span><span class="brand-name">Meadowlark Travel Co.</span></div>
    <nav class="nav">
      <svg class="home" viewBox="0 0 12 12"><path d="M6 1L1 5.5h1.5V11h3V8h1v3h3V5.5H11z" fill="#c49a4c"/></svg>
      <a>Brimwell Vacations</a><a class="active">Family Trips</a><a>Texas Road Trips</a><a>Other Destinations</a><a class="about">About Us</a>
      <span class="btn-contact">Contact Us <span class="arrow-dot"><svg viewBox="0 0 10 10"><path d="M2 8L8 2M3.5 2H8v4.5" fill="none" stroke="#fff" stroke-width="1.4"/></svg></span></span>
    </nav>
    <p class="eyebrow">OUR FAMILY TRIPS</p>
    <span class="spark hero-spark">✦</span>
    <h2 class="headline">EXPLORE UNIQUE<br>DESTINATIONS</h2>
    <p class="lede">The best family memories begin with meaningful adventures. Let us help you plan unforgettable trips designed around fun, comfort, and quality time together.</p>
    <div class="gallery">
      <div class="tile t1" role="img" aria-label="Family walking on a boardwalk between overwater villas"></div>
      <div class="tile t2 tall" role="img" aria-label="Family in life jackets kayaking near an island"></div>
      <div class="tile t3" role="img" aria-label="Family playing together on a sunny beach"></div>
      <div class="tile t4 tall" role="img" aria-label="Family relaxing on a sailboat deck"></div>
      <div class="tile t5" role="img" aria-label="Family viewing a historic European cathedral"></div>
      <div class="tile t6" role="img" aria-label="Mother and daughter overlooking a whitewashed seaside town"></div>
    </div>
    <form class="plan-card">
      <h3 class="plan-title">PLAN YOUR FAMILY TRIP</h3><span class="spark">✦</span>
      <label class="label" style="left:41px;top:89px">What Type of Trip Are You Interested In?</label>
      <label class="label" style="left:377px;top:89px">How Many People in Your Party?</label>
      <div class="field select" style="left:41px;top:116px;width:325px">Select<svg viewBox="0 0 14 14"><path d="M2 5l5 5 5-5" fill="none" stroke="#1d5a66" stroke-width="1.8"/></svg></div>
      <div class="field select" style="left:376px;top:115px;width:325px">Select<svg viewBox="0 0 14 14"><path d="M2 5l5 5 5-5" fill="none" stroke="#1d5a66" stroke-width="1.8"/></svg></div>
      <label class="label" style="left:41px;top:175px">What Kind of Trip Are You Looking For?</label>
      <label class="label" style="left:382px;top:175px">When Would You Like To Go?</label>
      <div class="field select" style="left:41px;top:200px;width:325px">Select<svg viewBox="0 0 14 14"><path d="M2 5l5 5 5-5" fill="none" stroke="#1d5a66" stroke-width="1.8"/></svg></div>
      <div class="field date" style="left:377px;top:200px;width:158px"><svg viewBox="0 0 14 14"><rect x="1.5" y="2.5" width="11" height="10" rx="1" fill="none" stroke="#8a9a9d"/><path d="M1.5 5.5h11M4 1v3M10 1v3" stroke="#8a9a9d"/></svg>Start Date</div>
      <div class="field date" style="left:542px;top:200px;width:158px"><svg viewBox="0 0 14 14"><rect x="1.5" y="2.5" width="11" height="10" rx="1" fill="none" stroke="#8a9a9d"/><path d="M1.5 5.5h11M4 1v3M10 1v3" stroke="#8a9a9d"/></svg>End Date</div>
      <label class="label" style="left:41px;top:251px">Any Additional Notes</label>
      <div class="field notes" style="left:41px;top:276px;width:660px">Type here</div>
      <div class="btn-plan">Start Planning <span class="arrow-dot"><svg viewBox="0 0 10 10"><path d="M2 8L8 2M3.5 2H8v4.5" fill="none" stroke="#fff" stroke-width="1.4"/></svg></span></div>
    </form>
    <footer class="footer"><p>© 2026 Meadowlark Travel Co. All Right Reserved</p><div class="social"><span></span><span></span></div></footer>
  </section>

  <section class="page page-right">
    <svg class="hills" viewBox="0 0 880 260" preserveAspectRatio="none" aria-hidden="true"><path d="M0 120 L160 60 L300 130 L420 80 L560 140 L700 70 L880 110 V260 H0Z" fill="#dfe8e7" opacity=".7"/><path d="M0 170 L200 120 L380 170 L560 130 L760 170 L880 150 V260 H0Z" fill="#d6e2e0" opacity=".6"/></svg>
    <div class="hero-photo" role="img" aria-label="Cheerful family in sunglasses and hats, child flying with outstretched arms"></div>
    <div class="contact-bar">
      <span><svg viewBox="0 0 20 20"><circle cx="10" cy="10" r="10" fill="#fff"/><rect x="5" y="6.5" width="10" height="7" rx="1" fill="none" stroke="#1d5a66" stroke-width="1.3"/><path d="M5.5 7l4.5 3.5L14.5 7" fill="none" stroke="#1d5a66" stroke-width="1.3"/></svg>hello@meadowlarktravel.example</span>
      <span><svg viewBox="0 0 20 20"><circle cx="10" cy="10" r="10" fill="#fff"/><path d="M7 5.5l2 2-1 1.5c.7 1.4 1.6 2.3 3 3l1.5-1 2 2-1.3 1.6c-3.5-.2-7-3.7-7.3-7.3z" fill="#1d5a66"/></svg>Phone Number (555) 010 2040</span>
    </div>
    <div class="brand"><span class="brand-dot"></span><span class="brand-name">Meadowlark Travel Co.</span></div>
    <nav class="nav">
      <svg class="home" viewBox="0 0 12 12"><path d="M6 1L1 5.5h1.5V11h3V8h1v3h3V5.5H11z" fill="#c49a4c"/></svg>
      <a>Brimwell Vacations</a><a class="active">Family Trips</a><a>Texas Road Trips</a><a>Other Destinations</a><a class="about">About Us</a>
      <span class="btn-contact">Contact Us <span class="arrow-dot"><svg viewBox="0 0 10 10"><path d="M2 8L8 2M3.5 2H8v4.5" fill="none" stroke="#fff" stroke-width="1.4"/></svg></span></span>
    </nav>
    <p class="eyebrow">OUR FAMILY TRIPS</p>
    <span class="spark hero-spark">✦</span>
    <h2 class="headline">EXPLORE UNIQUE<br>DESTINATIONS</h2>
    <p class="lede">The best family memories begin with meaningful adventures. Let us help you plan unforgettable trips designed around fun, comfort, and quality time together.</p>
    <div class="gallery">
      <div class="tile t1" role="img" aria-label="Family walking on a boardwalk between overwater villas"></div>
      <div class="tile t2 tall" role="img" aria-label="Family in life jackets kayaking near an island"></div>
      <div class="tile t3" role="img" aria-label="Family playing together on a sunny beach"></div>
      <div class="tile t4 tall" role="img" aria-label="Family relaxing on a sailboat deck"></div>
      <div class="tile t5" role="img" aria-label="Family viewing a historic European cathedral"></div>
      <div class="tile t6" role="img" aria-label="Mother and daughter overlooking a whitewashed seaside town"></div>
    </div>
    <form class="plan-card">
      <h3 class="plan-title">PLAN YOUR FAMILY TRIP</h3><span class="spark">✦</span>
      <label class="label" style="left:41px;top:89px">What Type of Trip Are You Interested In?</label>
      <label class="label" style="left:377px;top:89px">How Many People in Your Party?</label>
      <div class="field select" style="left:41px;top:116px;width:325px">Select<svg viewBox="0 0 14 14"><path d="M2 5l5 5 5-5" fill="none" stroke="#1d5a66" stroke-width="1.8"/></svg></div>
      <div class="field select" style="left:376px;top:115px;width:325px">Select<svg viewBox="0 0 14 14"><path d="M2 5l5 5 5-5" fill="none" stroke="#1d5a66" stroke-width="1.8"/></svg></div>
      <label class="label" style="left:41px;top:175px">What Kind of Trip Are You Looking For?</label>
      <label class="label" style="left:382px;top:175px">When Would You Like To Go?</label>
      <div class="field select" style="left:41px;top:200px;width:325px">Select<svg viewBox="0 0 14 14"><path d="M2 5l5 5 5-5" fill="none" stroke="#1d5a66" stroke-width="1.8"/></svg></div>
      <div class="field date" style="left:377px;top:200px;width:158px"><svg viewBox="0 0 14 14"><rect x="1.5" y="2.5" width="11" height="10" rx="1" fill="none" stroke="#8a9a9d"/><path d="M1.5 5.5h11M4 1v3M10 1v3" stroke="#8a9a9d"/></svg>Start Date</div>
      <div class="field date" style="left:542px;top:200px;width:158px"><svg viewBox="0 0 14 14"><rect x="1.5" y="2.5" width="11" height="10" rx="1" fill="none" stroke="#8a9a9d"/><path d="M1.5 5.5h11M4 1v3M10 1v3" stroke="#8a9a9d"/></svg>End Date</div>
      <label class="label" style="left:41px;top:251px">Any Additional Notes</label>
      <div class="field notes" style="left:41px;top:276px;width:660px">Type here</div>
      <div class="btn-plan">Start Planning <span class="arrow-dot"><svg viewBox="0 0 10 10"><path d="M2 8L8 2M3.5 2H8v4.5" fill="none" stroke="#fff" stroke-width="1.4"/></svg></span></div>
    </form>
    <footer class="footer"><p>© 2026 Meadowlark Travel Co. All Right Reserved</p><div class="social"><span></span><span></span></div></footer>
  </section>
</div>
</body>
</html>
```